Hunting Ethics Organization Needs a Web Design with Logo Refresh

This project involves the creation of a website design including the homepage design, inside page design, and logo refinements. Our organization is Tessaly, and we are a not-for-profit hunting ethics organization.
The focus of the new website design is to bring attention the mission of our organization, provide an overview of the areas where our organization deploys its resources to support the modern hunter, and to encourage visitors to support our organization by donating in support of the organization’s mission.
The winning design will be implemented in Wordpress by our in-house team. If you have questions about how any particular design element may translate to Wordpress, please feel free to post questions in response to this brief. In general, however, we’re more focused on the evolution and delivery of a strong overall design aesthetic – we’ll shoulder the responsibility of how we translate that design into Wordpress.
See attached design brief for full details.

```html
<!DOCTYPE html>
<html lang="en">
<head>
<meta charset="utf-8">
<title>Tessaly – Protecting the future of hunting</title>
<link href="https://fonts.googleapis.com/css2?family=Open+Sans:wght@400;600;700&display=swap" rel="stylesheet">
<style>
:root{
  --navy:#1c3a8c;
  --navy-dark:#142c6e;
  --nav-top:#2358ad;
  --nav-bottom:#153f8c;
  --green-top:#8cc63f;
  --green-bottom:#5f9e1c;
  --ink:#222;
  --body:#444;
  --footer:#1f1f1f;
  --footer-text:#8a8a8a;
  --white:#fff;
}
*{margin:0;padding:0;box-sizing:border-box}
html,body{width:1200px;height:2192px;overflow:hidden;background:var(--white)}
body{font-family:"Open Sans",sans-serif;color:var(--ink);position:relative}
.abs{position:absolute}

/* header */
.topline{left:0;top:0;width:1200px;height:3px;background:var(--navy)}
.site-header{left:0;top:3px;width:1200px;height:124px;background:var(--white)}
.brand{left:60px;top:18px;display:flex;align-items:center;gap:12px}
.brand-mark{width:44px;height:44px;border-radius:50%;background:var(--navy)}
.brand-name{font-size:48px;font-weight:600;color:var(--navy);line-height:1}
.brand-tagline{left:82px;top:88px;font-size:15px;color:var(--ink)}
.donate{left:563px;top:56px;width:168px;height:45px;background:linear-gradient(var(--green-top),var(--green-bottom));color:#fff;font-size:20px;display:flex;align-items:center;justify-content:center;border-radius:2px}
.social-dot{top:58px;width:46px;height:46px;border-radius:50%;border:3px solid #ddd;display:flex;align-items:center;justify-content:center}
.social-dot.a{left:754px;background:#2f4f91}
.social-dot.b{left:811px;background:#2a8fd6}
.social-dot.c{left:867px;background:#e14a24}
.search{left:935px;top:53px;width:206px;height:45px;border:2px solid #e2e2e2;display:flex;align-items:center;padding-left:18px;gap:10px;font-size:16px;color:#666}

/* nav */
.main-nav{left:0;top:127px;width:1200px;height:53px;background:linear-gradient(var(--nav-top),var(--nav-bottom))}
.main-nav a{position:absolute;top:14px;color:#fff;text-decoration:none;font-size:17px}

/* hero */
.hero{left:0;top:180px;width:1200px;height:438px;background:radial-gradient(ellipse at 65% 45%,#6a5a3e 0%,#3e3626 45%,#1f1c14 100%)}
.hero-panel{left:60px;top:262px;width:421px;height:285px;background:rgba(20,20,20,.72);padding:30px 22px 0 22px;color:#fff}
.hero-kicker{font-size:27px;font-weight:400;line-height:34px}
.hero-title{font-size:38px;font-weight:700;margin-top:8px;line-height:46px;white-space:nowrap}
.hero-text{font-size:13px;line-height:16px;margin-top:10px;width:385px}
.hero-btn{display:flex;align-items:center;justify-content:center;margin-top:24px;width:164px;height:55px;background:var(--navy);color:#fff;font-size:21px;font-weight:600;border-radius:2px}
.dot{top:578px;width:17px;height:17px;border-radius:50%;background:#c8c8c8}
.dot.active{background:var(--navy)}

/* welcome */
.welcome-title{left:0;top:660px;width:1200px;text-align:center;font-size:34px;font-weight:400}
.welcome-text{left:60px;top:718px;width:1080px;text-align:center;font-size:13.5px;line-height:22px;color:var(--body)}
.btn-navy{background:var(--navy);color:#fff;font-size:16px;font-weight:600;display:flex;align-items:center;justify-content:center;border-radius:3px}
.welcome-btn{left:544px;top:785px;width:112px;height:45px}

/* pillars */
.pillars{left:0;top:893px;width:1200px;height:361px;background:linear-gradient(#3d3a35 0%,#544a3c 45%,#2f3322 80%,#222818 100%)}
.pillar{top:953px;width:320px;height:238px;background:rgba(40,40,40,.72);text-align:center;color:#fff;padding-top:34px}
.pillar h3{font-size:28px;font-weight:400}
.pillar p{font-size:13.5px;line-height:22px;color:#ddd;margin:20px 18px 0}
.pillar .more{display:block;font-size:15px;margin-top:28px}

/* stories */
.stories-title{left:62px;top:1300px;font-size:34px;font-weight:400}
.story{top:1386px;width:339px}
.story-img{width:339px;height:203px}
.story h4{font-size:23px;font-weight:600;line-height:34px;color:var(--navy);margin-top:24px}
.story p{font-size:13.5px;line-height:22px;color:var(--body);margin-top:14px}
.story .more{display:inline-block;margin-top:14px;font-size:15px;color:var(--navy);text-decoration:underline}

/* footer */
.site-footer{left:0;top:1836px;width:1200px;height:356px;background:var(--footer)}
.footer-brand{left:60px;top:1918px;display:flex;align-items:center;gap:12px}
.footer-brand .brand-mark{background:#0f0f0f}
.footer-brand .brand-name{color:#0f0f0f}
.footer-col{top:1880px;color:var(--footer-text);font-size:13px;line-height:22px}
.footer-col h5{font-size:28px;font-weight:400;color:#fff;margin-bottom:12px;line-height:38px}
.mail-input{width:256px;height:39px;background:#fff;font-size:13px;color:#666;padding:9px 14px;margin-top:18px}
.submit{width:82px;height:44px;margin-top:21px}
.sq{top:1972px;width:66px;height:54px;background:#363636;display:flex;align-items:center;justify-content:center}
.footer-rule{left:0;top:2115px;width:1200px;height:1px;background:#333}
.copyright{left:0;top:2139px;width:1200px;text-align:center;font-size:13px;color:#777}
</style>
</head>
<body>

<div class="abs topline"></div>
<header class="abs site-header"></header>
<div class="abs brand"><span class="brand-mark"></span><span class="brand-name">Tessaly</span></div>
<div class="abs brand-tagline">Protecting the future of hunting.</div>
<div class="abs donate">Donate Now</div>
<div class="abs social-dot a" role="img" aria-label="Share link">
  <svg width="20" height="20" viewBox="0 0 20 20" fill="none" stroke="#fff" stroke-width="2.2" stroke-linecap="round"><path d="M8 12l4-4"/><path d="M9 5l2-2a3.5 3.5 0 015 5l-2 2"/><path d="M11 15l-2 2a3.5 3.5 0 01-5-5l2-2"/></svg>
</div>
<div class="abs social-dot b" role="img" aria-label="Message link">
  <svg width="20" height="20" viewBox="0 0 20 20"><path d="M3 4h14v9H8l-4 3v-3H3z" fill="#fff"/></svg>
</div>
<div class="abs social-dot c" role="img" aria-label="News feed">
  <svg width="18" height="18" viewBox="0 0 18 18" fill="#fff"><rect x="2" y="3" width="14" height="2.4" rx="1"/><rect x="2" y="8" width="14" height="2.4" rx="1"/><rect x="2" y="13" width="9" height="2.4" rx="1"/></svg>
</div>
<div class="abs search">
  <svg width="14" height="14" viewBox="0 0 14 14"><circle cx="6" cy="6" r="4.5" fill="none" stroke="#888" stroke-width="2"/><line x1="9.5" y1="9.5" x2="13" y2="13" stroke="#888" stroke-width="2"/></svg>
  Search
</div>

<nav class="abs main-nav">
  <a style="left:60px">Home</a>
  <a style="left:149px">About Us</a>
  <a style="left:263px">Hunting Ethics</a>
  <a style="left:417px">Conservation</a>
  <a style="left:563px">Get Involved</a>
  <a style="left:702px">Contact Us</a>
</nav>

<section class="abs hero" role="img" aria-label="Photo of a mallard duck in flight over a blurred autumn background"></section>
<div class="abs hero-panel">
  <div class="hero-kicker">Protect the</div>
  <div class="hero-title">Heritage of Hunting</div>
  <p class="hero-text">and to encourage visitors to support our organization by donating in support of the organization's mission</p>
  <span class="hero-btn">Get Involved</span>
</div>
<span class="abs dot" style="left:550px"></span>
<span class="abs dot active" style="left:591px"></span>
<span class="abs dot" style="left:631px"></span>

<h2 class="abs welcome-title">Welcome to Tessaly</h2>
<p class="abs welcome-text">Tessaly's customer/audience is the hunter. Tessaly does not cater to any particular type of hunter (eg; not just deer hunters or bird hunters) but rather all hunters. The website design should therefore provide appeal across all types of hunting.</p>
<div class="abs btn-navy welcome-btn">Read More</div>

<section class="abs pillars" role="img" aria-label="Photo of deer grazing in a field at dusk"></section>
<div class="abs pillar" style="left:60px"><h3>Hunting Ethics</h3><p>Neque porro quisquam est, qui dolorem ipsum quia dolor sit amet, consectetur, adipisci velit, sed quia non numquam</p><span class="more">Read More</span></div>
<div class="abs pillar" style="left:440px"><h3>Conservation</h3><p>Neque porro quisquam est, qui dolorem ipsum quia dolor sit amet, consectetur, adipisci velit, sed quia non numquam</p><span class="more">Read More</span></div>
<div class="abs pillar" style="left:818px"><h3>Get Involved</h3><p>Neque porro quisquam est, qui dolorem ipsum quia dolor sit amet, consectetur, adipisci velit, sed quia non numquam</p><span class="more">Read More</span></div>

<h2 class="abs stories-title">Top Stories</h2>
<article class="abs story" style="left:60px">
  <div class="story-img" role="img" aria-label="Photo of a hunter aiming a rifle in green ferns" style="background:linear-gradient(135deg,#4f8a2a,#2e5a1a)"></div>
  <h4>Et harum quidem rerum facilis est et expedita distinctio</h4>
  <p>Neque porro quisquam est, qui dolorem ipsum quia dolor sit amet, consectetur, adipisci velit...</p>
  <span class="more">Read More</span>
</article>
<article class="abs story" style="left:431px">
  <div class="story-img" role="img" aria-label="Photo of a retriever dog carrying a bird" style="background:radial-gradient(circle at 55% 55%,#8a6a3a,#4a2e14)"></div>
  <h4>Et harum quidem rerum facilis est et expedita distinctio</h4>
  <p>Neque porro quisquam est, qui dolorem ipsum quia dolor sit amet, consectetur, adipisci velit...</p>
  <span class="more">Read More</span>
</article>
<article class="abs story" style="left:800px">
  <div class="story-img" role="img" aria-label="Photo of giraffes in a savanna at sunset" style="background:linear-gradient(160deg,#e0a53a,#a8621c 60%,#4a5a1e)"></div>
  <h4>Et harum quidem rerum facilis est et expedita distinctio</h4>
  <p>Neque porro quisquam est, qui dolorem ipsum quia dolor sit amet, consectetur, adipisci velit...</p>
  <span class="more">Read More</span>
</article>

<footer class="abs site-footer"></footer>
<div class="abs footer-brand"><span class="brand-mark"></span><span class="brand-name">Tessaly</span></div>
<div class="abs footer-col" style="left:345px">
  <h5>Stay Informed</h5>
  <p>Sign up for breaking news on wildlife and<br>conservation issues:</p>
  <div class="mail-input">Enter Your Mail ID</div>
  <div class="btn-navy submit">Submit</div>
</div>
<div class="abs footer-col" style="left:650px">
  <h5>Connect With Us</h5>
  <p>Follow Tessaly on our social media sites:</p>
</div>
<div class="abs sq" style="left:658px" role="img" aria-label="Share link">
  <svg width="22" height="22" viewBox="0 0 20 20" fill="none" stroke="#fff" stroke-width="2.2" stroke-linecap="round"><path d="M8 12l4-4"/><path d="M9 5l2-2a3.5 3.5 0 015 5l-2 2"/><path d="M11 15l-2 2a3.5 3.5 0 01-5-5l2-2"/></svg>
</div>
<div class="abs sq" style="left:737px" role="img" aria-label="Message link">
  <svg width="22" height="22" viewBox="0 0 20 20"><path d="M3 4h14v9H8l-4 3v-3H3z" fill="#fff"/></svg>
</div>
<div class="abs sq" style="left:814px" role="img" aria-label="News feed">
  <svg width="20" height="20" viewBox="0 0 18 18" fill="#fff"><rect x="2" y="3" width="14" height="2.4" rx="1"/><rect x="2" y="8" width="14" height="2.4" rx="1"/><rect x="2" y="13" width="9" height="2.4" rx="1"/></svg>
</div>
<div class="abs footer-col" style="left:940px">
  <h5>Contact us</h5>
  <p>Nemo enim ipsam voluptatem<br>quia voluptast</p>
  <p style="margin-top:22px">1800-555-014<br>hello@tessaly-example.org</p>
</div>
<div class="abs footer-rule"></div>
<div class="abs copyright">©2015 Tessaly. All rights reserved.</div>

</body>
</html>
```